Digital One Pager for Consulting Practice

I would like the essence of the content in my ppt consolidated into a one-pager. The one-pager will mainly be sent via email as a pdf and intended to excite and invite new clients and establish the credibility of my boutique high-end consulting firm. Infographics and symbols would be a plus. The target client should view the firm as providing premeir service. The client is getting a thought partner.

Target Market(s)

Large Medical Device Manufacturer Executives, Early-Stage Medical Device Manufacturer Executives, Partners at VC Firms

Industry/Entity Type

Medical Equipment

Colors
0355a3
f37122

Requirements
Must have
• Please match the color scheme in ppt. Please use the existing logo. I am very open to better graphics on the process. My photo does not need to be on the digital flyer. Hyper link to the website and email is needed.
Nice to have
• Infographics

```html
<!DOCTYPE html>
<html lang="en">
<head>
<meta charset="utf-8">
<title>Harlow Advisory – Website and One Pager</title>
<link rel="stylesheet" href="https://fonts.googleapis.com/css2?family=Jost:wght@400;500;600&family=Source+Serif+4:opsz,wght@8..60,400;8..60,600;8..60,700&display=swap">
<style>
  :root{
    --navy:#0b1a33;
    --orange:#ee4623;
    --ink:#1d2433;
    --muted:#5b6270;
    --rule:#c9ccd2;
    --page:#f2f2f2;
    --paper:#ffffff;
    --stone:#8e9097;
    --serif:"Source Serif 4", Georgia, serif;
    --sans:"Jost", Arial, sans-serif;
  }
  *{box-sizing:border-box;margin:0;padding:0}
  html,body{width:1200px;height:731px;overflow:hidden}
  body{background:var(--page);font-family:var(--sans);color:var(--ink);position:relative}
  a{color:inherit;text-decoration:none}

  /* ---------- Website page ---------- */
  .site{position:absolute;left:108px;top:186px;width:563px;height:351px;background:#f3f3f4;overflow:hidden;box-shadow:0 6px 24px rgba(0,0,0,.08)}
  .site h2{font-family:var(--serif);font-weight:400;font-size:17px;color:var(--ink)}
  .site .label{font-size:5px;font-weight:600;letter-spacing:.06em;color:var(--orange);text-transform:uppercase}
  .site p{font-size:5.4px;line-height:1.55;color:var(--muted)}
  .approach{position:absolute;left:44px;top:78px;width:270px}
  .approach p{margin-top:28px}
  .btn-more{display:inline-block;margin-top:14px;border:1px solid var(--ink);width:61px;height:27px;line-height:25px;text-align:center;font-size:5px;font-weight:600;letter-spacing:.1em}
  .site-contact{position:absolute;left:370px;top:78px}
  .site-contact .label{margin-top:16px}
  .site-contact .line{font-family:var(--serif);font-size:9.5px;margin-top:9px}
  .expertise{position:absolute;left:44px;top:278px;width:475px}
  .expertise .rules{display:flex;gap:14px;margin-top:16px}
  .expertise .rules span{width:149px;border-top:1px solid var(--rule)}
  .expertise .cols{display:flex;gap:14px}
  .expertise .col{width:149px;margin-top:16px}
  .expertise .col p{margin-top:7px}

  /* ---------- One pager ---------- */
  .onepager{position:absolute;left:758px;top:118px;width:355px;height:502px;background:var(--paper);overflow:hidden;box-shadow:0 10px 30px rgba(0,0,0,.16)}
  .hero{position:absolute;left:0;top:0;width:355px;height:98px;background:linear-gradient(120deg,#16294a 0%,#0c1c38 55%,#1e3356 100%)}
  .hero-curve{position:absolute;left:0;top:0}
  .hero-band{position:absolute;left:0;top:98px;width:355px;height:4px;background:var(--orange)}
  .brand-mark{position:absolute;right:14px;top:28px;font-family:var(--sans);font-weight:600;font-size:11px;letter-spacing:.05em;color:var(--navy);line-height:1.05;text-align:right}
  .hero-kicker{position:absolute;left:24px;top:40px;font-size:9.5px;font-weight:500;letter-spacing:.12em;color:var(--orange)}
  .hero-title{position:absolute;left:23px;top:49px;font-family:var(--serif);font-weight:700;font-size:31px;color:#fff;letter-spacing:-.01em}

  .col-left{position:absolute;left:0;top:102px;width:177px;height:400px}
  .col-right{position:absolute;left:177px;top:102px;width:178px;height:400px;background:var(--navy);color:#fff}
  .onepager h3{font-family:var(--serif);font-weight:400;font-size:13px;color:var(--ink);padding-bottom:5px;border-bottom:1px solid var(--rule);width:144px}
  .col-right h3{color:#fff;border-bottom-color:rgba(255,255,255,.28)}

  .ticks{list-style:none;margin-top:7px;width:140px}
  .ticks li{position:relative;padding-left:11px;margin-bottom:6px;font-size:4.6px;line-height:1.35}
  .ticks li svg{position:absolute;left:0;top:0}
  .ticks b{font-weight:600;letter-spacing:.03em;text-transform:uppercase}
  .ticks span{display:block}

  .services{list-style:none;margin-top:9px;width:140px}
  .services li{position:relative;padding-left:16px;margin-bottom:7px;font-size:4.6px;line-height:1.35}
  .services li svg{position:absolute;left:0;top:0}
  .services b{font-weight:600;letter-spacing:.03em;text-transform:uppercase;display:block}

  .sec-exp{position:absolute;left:24px;top:15px}
  .sec-services{position:absolute;left:24px;top:131px}
  .sec-partners{position:absolute;left:24px;top:292px}
  .partners{display:grid;grid-template-columns:repeat(3,38px);gap:8px 9px;margin-top:12px}
  .badge{height:14px;border-radius:2px}
  .badge.light{background:#dcdde1}
  .badge.dark{background:#2b2d33}
  .badge.round{border-radius:7px}

  .sec-provide{position:absolute;left:22px;top:15px}
  .sec-process{position:absolute;left:22px;top:131px}
  .sec-chat{position:absolute;left:22px;top:292px}
  .chat-label{font-size:4.8px;font-weight:600;letter-spacing:.08em;color:var(--orange);margin-top:9px}
  .chat-lines{margin-top:4px;font-family:var(--serif);font-size:7.6px;line-height:1.75}
  .process{display:block;margin-top:4px}
  .process text{font-family:"Jost", Arial, sans-serif}
</style>
</head>
<body>

<section class="site" aria-label="Website page">
  <div class="approach">
    <h2>Our Approach</h2>
    <p>We engage our clients to gain a deep and clear understanding of their needs. This rigorous discovery process serves as the starting point to develop solutions that deliver for the client and meet the requirements of the regulatory agency. Consultants use a consistent set of tools to solve your problems, consider an exhaustive range of factors to manage risks and unearth opportunities for the customer.</p>
    <a class="btn-more" href="https://www.harlowadvisory.com">LEARN MORE</a>
  </div>
  <div class="site-contact">
    <h2>Contact</h2>
    <div class="label">Contact</div>
    <div class="line"><a href="mailto:info@harlowadvisory.com">info@harlowadvisory.com</a></div>
    <div class="line">+1 202.555.0148</div>
  </div>
  <div class="expertise">
    <h2>Areas of Expertise</h2>
    <div class="rules"><span></span><span></span><span></span></div>
    <div class="cols">
      <div class="col"><div class="label">Strategy</div><p>Consultants develop a regulatory path that manages</p></div>
      <div class="col"><div class="label">FDA Communication</div><p>We prepare the company for effective interactions with</p></div>
      <div class="col"><div class="label">Regulatory Diligence</div><p>At Harlow Advisory, experienced consultants evaluate</p></div>
    </div>
  </div>
</section>

<article class="onepager" aria-label="Harlow Advisory one pager">
  <div class="hero" role="img" aria-label="Dark blue photo of hands working on a laptop"></div>
  <svg class="hero-curve" width="355" height="102" viewBox="0 0 355 102" aria-hidden="true">
    <path d="M208 0 C 248 52, 296 84, 355 94 L355 0 Z" fill="#ffffff"/>
  </svg>
  <div class="hero-band"></div>
  <div class="brand-mark">HARLOW<br>ADVISORY</div>
  <div class="hero-kicker">HARLOW ADVISORY</div>
  <div class="hero-title">Value.</div>

  <div class="col-left">
    <div class="sec-exp">
      <h3>Experience</h3>
      <ul class="ticks">
        <li><svg width="7" height="7" viewBox="0 0 10 10"><circle cx="5" cy="5" r="5" fill="#ee4623"/><path d="M2.8 5.2l1.6 1.6 3-3.2" stroke="#fff" stroke-width="1.3" fill="none"/></svg><b>Over a decade @FDA</b><span>(Former Deputy Division Director)</span></li>
        <li><svg width="7" height="7" viewBox="0 0 10 10"><circle cx="5" cy="5" r="5" fill="#ee4623"/><path d="M2.8 5.2l1.6 1.6 3-3.2" stroke="#fff" stroke-width="1.3" fill="none"/></svg><b>Expertise:</b> Cardiovascular, Ophthalmology, General Hospital, Infection Control, Dental, Anesthesia, Respiratory</li>
        <li><svg width="7" height="7" viewBox="0 0 10 10"><circle cx="5" cy="5" r="5" fill="#ee4623"/><path d="M2.8 5.2l1.6 1.6 3-3.2" stroke="#fff" stroke-width="1.3" fill="none"/></svg><b>Vice President Regulatory Affairs / Quality Assurance @Corvane (Fortune 150 Company)</b><span>- Initiated reorganization of department</span><span>- Led major compliance effort</span><span>- Successful FDA inspection (no observations)</span></li>
      </ul>
    </div>

    <div class="sec-services">
      <h3>Services</h3>
      <ul class="services">
        <li><svg width="9" height="7" viewBox="0 0 9 7"><path d="M0.5 0v6.5h8" stroke="#ee4623" fill="none"/><rect x="2" y="3" width="1.2" height="3" fill="#ee4623"/><rect x="4" y="1.5" width="1.2" height="4.5" fill="#ee4623"/><rect x="6" y="2.5" width="1.2" height="3.5" fill="#ee4623"/></svg><b>Regulatory Strategy</b>• RAQA Organizational Structure<br>• Regulatory Pathway</li>
        <li><svg width="9" height="7" viewBox="0 0 9 7"><rect x="0.5" y="0.5" width="6" height="4" rx="1" stroke="#ee4623" fill="none"/><path d="M2 4.5v2l2-2" stroke="#ee4623" fill="none"/></svg><b>FDA Communications</b>• Deficiency Response<br>• Application Review</li>
        <li><svg width="9" height="7" viewBox="0 0 9 7"><circle cx="4" cy="2.2" r="1.7" stroke="#ee4623" fill="none"/><path d="M1 6.6c0-1.8 1.3-2.6 3-2.6s3 .8 3 2.6z" stroke="#ee4623" fill="none"/></svg><b>Interim Executive Leadership</b>• Compliance Remediation<br>• Accelerated Product Registration</li>
        <li><svg width="9" height="7" viewBox="0 0 9 7"><rect x="1" y="1" width="5" height="5.6" stroke="#ee4623" fill="none"/><rect x="2.3" y="0.2" width="2.4" height="1.4" fill="#ee4623"/></svg><b>Training</b>• FDA Communication<br>• MDR Reporting</li>
      </ul>
    </div>

    <div class="sec-partners">
      <h3>Valued Partner Network</h3>
      <div class="partners">
        <div class="badge light round"></div>
        <div class="badge dark"></div>
        <div class="badge light"></div>
        <div class="badge light round"></div>
        <div class="badge dark"></div>
        <div class="badge light"></div>
      </div>
    </div>
  </div>

  <div class="col-right">
    <div class="sec-provide">
      <h3>Experience to Provide</h3>
      <ul class="ticks">
        <li><svg width="7" height="7" viewBox="0 0 10 10"><circle cx="5" cy="5" r="5" fill="#ee4623"/><path d="M2.8 5.2l1.6 1.6 3-3.2" stroke="#fff" stroke-width="1.3" fill="none"/></svg><b>Executive Application Review</b><span>- Examples include: Presubmission, IDE, 510(k), 513(g), PMA, Refuse to Accept, Hold letter</span><span>- Troubleshooting</span></li>
        <li><svg width="7" height="7" viewBox="0 0 10 10"><circle cx="5" cy="5" r="5" fill="#ee4623"/><path d="M2.8 5.2l1.6 1.6 3-3.2" stroke="#fff" stroke-width="1.3" fill="none"/></svg><b>Strategic Advice &amp; Diligence to Investors</b><span>- Validate &amp; Verify Founder Milestones</span><span>- Diligence-portfolio company Regulatory and Quality systems</span></li>
      </ul>
    </div>

    <div class="sec-process">
      <h3>Efficient Process</h3>
      <svg class="process" width="140" height="130" viewBox="0 0 140 130" aria-label="Four step process: exploratory call, regulatory landscape, problem statement, review and align on deliverables">
        <path d="M30 16 L79 42 L30 69 L79 93" stroke="#ffffff" stroke-width="9" fill="none" stroke-linejoin="round"/>
        <path d="M30 16 L79 42 L30 69 L79 93" stroke="#8e9097" stroke-width="5" fill="none" stroke-linejoin="round"/>

        <rect x="34" y="8" width="82" height="16" rx="8" fill="#ee4623"/>
        <text x="50" y="15" font-size="4.6" fill="#fff">Exploratory</text>
        <text x="50" y="20.5" font-size="4.6" fill="#fff">Call</text>
        <rect x="98" y="12" width="11" height="7" rx="2" fill="none" stroke="#fff" stroke-width=".8"/>
        <path d="M101 19v2.2l2-2.2" stroke="#fff" stroke-width=".8" fill="none"/>
        <circle cx="30" cy="16" r="13" fill="#ee4623" stroke="#fff" stroke-width="2.5"/>
        <text x="30" y="19.5" text-anchor="middle" font-weight="600" font-size="10" fill="#fff">01</text>

        <rect x="0" y="34" width="80" height="16" rx="8" fill="#8e9097"/>
        <rect x="5" y="38" width="10" height="7" fill="none" stroke="#fff" stroke-width=".8"/>
        <path d="M5 38l5 4 5-4" stroke="#fff" stroke-width=".8" fill="none"/>
        <text x="20" y="41" font-size="4.6" fill="#fff">Regulatory</text>
        <text x="20" y="46.5" font-size="4.6" fill="#fff">Landscape</text>
        <circle cx="79" cy="42" r="13" fill="#8e9097" stroke="#fff" stroke-width="2.5"/>
        <text x="79" y="45.5" text-anchor="middle" font-weight="600" font-size="10" fill="#fff">02</text>

        <rect x="34" y="61" width="82" height="16" rx="8" fill="#ee4623"/>
        <text x="50" y="68" font-size="4.6" fill="#fff">Problem</text>
        <text x="50" y="73.5" font-size="4.6" fill="#fff">Statement</text>
        <rect x="99" y="63.5" width="8" height="10" fill="none" stroke="#fff" stroke-width=".8"/>
        <path d="M100.5 66.5h5M100.5 68.5h5M100.5 70.5h5" stroke="#fff" stroke-width=".6"/>
        <circle cx="30" cy="69" r="13" fill="#ee4623" stroke="#fff" stroke-width="2.5"/>
        <text x="30" y="72.5" text-anchor="middle" font-weight="600" font-size="10" fill="#fff">03</text>

        <rect x="0" y="85" width="80" height="16" rx="8" fill="#8e9097"/>
        <path d="M10 98c-3-3.5-4-5-4-6.5a4 4 0 0 1 8 0c0 1.5-1 3-4 6.5z" fill="none" stroke="#fff" stroke-width=".8"/>
        <circle cx="10" cy="91.5" r="1.2" fill="#fff"/>
        <text x="20" y="92" font-size="4.6" fill="#fff">Review &amp; Align</text>
        <text x="20" y="97.5" font-size="4.6" fill="#fff">on Deliverables</text>
        <circle cx="79" cy="93" r="13" fill="#8e9097" stroke="#fff" stroke-width="2.5"/>
        <text x="79" y="96.5" text-anchor="middle" font-weight="600" font-size="10" fill="#fff">04</text>
      </svg>
    </div>

    <div class="sec-chat">
      <h3>Let's Chat</h3>
      <div class="chat-label">CONTACT</div>
      <div class="chat-lines">
        <div>+1 202.555.0148</div>
        <div><a href="mailto:info@harlowadvisory.com">info@harlowadvisory.com</a></div>
        <div><a href="https://www.harlowadvisory.com">harlowadvisory.com</a></div>
      </div>
    </div>
  </div>
</article>

</body>
</html>
```